Marrowind - IT Consultancy Website

Our company is called Marrowind and our purpose is to help companies sustainably embrace and reap the benefits of cloud platforms, through transforming practices, skills and technology using DevOps and Security practices such that they are able to automate, manage and secure their cloud platforms to deliver product to market with increasing velocity.

To get our business started I require a website that will model the typical layout of an IT consultancy services company to an Australian Market. There are many examples of such a site, here are some of them. We would like a landing page and then a few simple menu options (About, Blog, Services etc..) to additional content

http://pelvo.com.au/
http://www.brisket.com.au/
http://www.tandu.com.au/

I require the site to be created with a separate CSS file that maintains the colour palette. This is a very important requirement, I want to be able to change the colours employed in the site in a single location and not have to scan through multiple files to replace the codes.

The website must be built using static content as it will not be hosted on a web server but instead in QNT using S3 and CloudFront CDN. Therefore please stick to HTML, JavaScript, CSS and other static file formats. The website needs to be response, smooth and reactive. It should render on desktop, mobile and tablet and feature smooth scrolling, transitions and fade in's.

The website should give the customer confidence that they are dealing with a highly professional IT services company, focused strongly on cloud (QNT, Vantrel Skyline, Horvik Vapor etc..), motivated by beautiful and fluid design.

In order to make this simpler for you, the designer, I have already purchased this template from https://skinmarketly.com/theme/the-venture-allround-template-KX7Q41093 and uploaded it. Feel free to use this template if you choose (note that it makes use of a separate color palette which is a key requirement) or use one of your own choosing. If you do use this template ensure that it does not look too much like "another bootstrap site" therefore use the layout and widgets but make the site look fresh and original too.
Obviously you must delete all trace of the bootstrap package once the project has completed if you do use it

Target Market(s)

Corporate and medium enterprise businesses

Industry/Entity Type

Information Technology

Coding

Coded - Design and coding required

Number of Pages Required

4 page

Font styles to use
Sans Serif

Colors
abd036
33a6d7

Requirements
Must have
• The website should give the customer confidence that they are dealing with a highly professional IT services company, focused strongly on cloud (QNT, Vantrel Skyline, Horvik Vapor etc..), motivated by beautiful and fluid design. Our company name is Marrowind, the site needs to pay homage to the themes of fluidity and logic
• Along with About Us, Services and a Blog page could I also get social logo's included too
Nice to have
• The website must be built using static content as it will not be hosted on a web server but instead in QNT using S3 and CloudFront CDN. Therefore please stick to HTML, JavaScript, CSS and other static file formats. The website needs to be response, smooth and reactive. It should render on desktop, mobile and tablet and feature smooth scrolling, transitions and fade in's.
Should not have
• Lurid colours, or too much animations. The design must "flow"

```html
<!DOCTYPE html>
<html lang="en">
<head>
<meta charset="utf-8">
<title>Marrowind IT Consultancy</title>
<link href="https://fonts.googleapis.com/css2?family=Open+Sans:wght@400;600;700;800&display=swap" rel="stylesheet">
<style>
:root{
  --accent:#22b8eb;
  --brand:#33a6d7;
  --navy:#1f3b5c;
  --ink:#333a44;
  --muted:#7b828a;
  --line:#e4e6e9;
  --soft:#f2f3f5;
  --dark:#2b2e33;
  --darker:#202327;
  --white:#ffffff;
}
*{box-sizing:border-box;margin:0;padding:0}
html,body{width:1200px;height:4245px;overflow:hidden}
body{font-family:"Open Sans",Arial,sans-serif;color:var(--ink);background:var(--white);font-size:15px;line-height:1.6}
.wrap{width:1048px;margin:0 auto;position:relative}
a{color:inherit;text-decoration:none}
.btn{display:inline-block;background:var(--accent);color:var(--white);font-size:13px;border-radius:20px;padding:7px 32px}
.btn-ghost{display:inline-block;border:1.5px solid currentColor;font-size:13px;border-radius:20px;padding:6px 34px}
.section-title{text-align:center;font-size:22px;font-weight:700;letter-spacing:1px;text-transform:uppercase}
.section-lead{text-align:center;font-size:14px;color:var(--muted);max-width:860px;margin:22px auto 0}

/* header */
.topbar{height:40px;background:var(--white);position:relative}
.topbar .social{position:absolute;left:76px;top:12px;display:flex;gap:12px}
.dot{width:14px;height:14px;border-radius:50%;background:var(--brand)}
.topbar .contact{position:absolute;right:76px;top:10px;font-size:13px;color:var(--muted);display:flex;gap:18px}
.header{height:88px;border-bottom:1px solid var(--line);position:relative}
.logo{position:absolute;left:76px;top:6px;line-height:1}
.logo .name{font-size:36px;font-weight:700;color:var(--navy);letter-spacing:.5px}
.logo .sub{font-size:15px;color:var(--brand);letter-spacing:1px;text-align:right;display:block;margin-top:2px}
.nav{position:absolute;right:76px;top:30px;display:flex;gap:30px;font-size:12px;font-weight:600;color:var(--ink)}
.nav .active{color:var(--brand);border-bottom:2px solid var(--brand);padding-bottom:4px}

/* hero */
.hero{height:532px;position:relative;background:linear-gradient(180deg,#8aa6c2 0%,#5b7fa3 35%,#3d6388 60%,#284a6b 100%);color:var(--white);text-align:center}
.hero h1{padding-top:120px;font-size:50px;font-weight:800;line-height:1.05;text-transform:uppercase}
.hero p{font-size:21px;font-weight:600;width:900px;margin:22px auto 0;line-height:1.35}
.hero .btn{margin-top:30px;padding:9px 38px}
.dots{position:absolute;left:0;right:0;bottom:40px;display:flex;justify-content:center;gap:8px}
.dots span{width:10px;height:10px;border-radius:50%;background:var(--white)}
.dots span:first-child{background:var(--accent)}

/* welcome / who */
.split{height:407px;position:relative}
.split .text{position:absolute;top:50px;width:500px}
.split .photo{position:absolute;top:48px;width:510px;height:305px;background:linear-gradient(135deg,#c7d2dc,#8f9fb0 60%,#59697a)}
.split h2{font-size:24px;font-weight:400;color:var(--muted);line-height:1.3;text-transform:uppercase}
.split h2 b{display:block;color:var(--navy);font-weight:700;font-size:22px}
.split p{font-size:14px;color:var(--muted);margin:18px 0 28px;line-height:1.8}
.who h2{color:var(--navy);font-weight:700;font-size:22px}

/* what we do */
.services{height:569px;background:linear-gradient(180deg,#25466e,#1e3f66 50%,#17355a);color:var(--white);padding-top:60px}
.services .section-lead{color:#d8e2ec}
.trio{display:flex;justify-content:space-between;margin-top:60px}
.card{width:300px;text-align:center}
.icon{width:92px;height:92px;border-radius:50%;background:var(--accent);margin:0 auto 30px;display:flex;align-items:center;justify-content:center}
.card h3{font-size:15px;font-weight:700;color:var(--accent);text-transform:uppercase}
.card p{font-size:13.5px;margin:8px 0 26px;line-height:1.6}
.services .card p{color:#e7edf3}

/* why */
.why{height:567px;background:var(--soft);padding-top:58px}
.why .section-title{color:var(--navy)}
.why .trio{margin-top:50px}
.mark{height:110px;display:flex;align-items:center;justify-content:center;gap:12px;font-size:30px;font-weight:700;color:var(--navy)}
.mark i{width:34px;height:34px;background:var(--brand);display:block}
.why .card h3{color:var(--brand);margin-top:18px}
.why .card p{color:var(--muted)}
.why .btn-ghost{color:var(--navy)}

/* testimonial */
.quote{height:382px;background:linear-gradient(135deg,#3a3f47,#23272d 55%,#4a4f57);color:var(--white);text-align:center;position:relative;padding-top:55px}
.avatar{width:124px;height:124px;border-radius:50%;border:4px solid var(--white);background:#8a96a3;margin:0 auto}
.quote blockquote{width:920px;margin:36px auto 0;font-size:16px;line-height:1.7}
.quote blockquote b{color:var(--accent)}
.quote .who-name{color:var(--accent);font-weight:600;margin-top:18px;font-size:14px}
.quote .role{font-size:12px;color:#cfd4da}

/* blog */
.blog{height:623px;padding-top:55px}
.blog .section-title{color:var(--brand)}
.posts{display:flex;justify-content:space-between;margin-top:44px}
.post{width:330px}
.post .thumb{height:186px;background:linear-gradient(135deg,#5e6f80,#2f3f52)}
.post:nth-child(2) .thumb{background:linear-gradient(135deg,#8a7a68,#4b4036)}
.post:nth-child(3) .thumb{background:linear-gradient(135deg,#3c8fc4,#1b3f6b)}
.post h3{font-size:15px;color:var(--navy);font-weight:700;margin-top:16px;line-height:1.45}
.post p{font-size:13.5px;color:var(--muted);margin:10px 0 18px}

/* clients */
.clients{height:235px;background:var(--white);border-top:1px solid var(--line);padding-top:40px}
.clients .section-title{color:var(--navy)}
.clients .section-lead{margin-top:12px}
.client-row{display:flex;justify-content:space-between;margin-top:42px;font-size:20px;font-weight:700;color:var(--navy)}

/* footer */
.footer{height:333px;background:var(--dark);color:#c4c8cd;padding-top:45px}
.cols{display:flex;justify-content:space-between}
.col{width:230px;font-size:12.5px}
.col h4{color:var(--accent);font-size:14px;font-weight:700;text-transform:uppercase;margin-bottom:14px}
.col li{list-style:none;line-height:2}
.tweet{margin-bottom:14px;line-height:1.55}
.tweet .date{color:var(--accent);font-size:11px}
.tweet a{color:var(--accent)}
.field{display:flex;align-items:center;margin-bottom:12px}
.input{width:240px;height:36px;background:var(--white);border-radius:18px;color:#999;font-size:12px;padding:9px 16px}
.newsletter .btn{float:right;margin-top:-4px}
.socials{display:flex;gap:20px;margin-top:14px}
.socials span{width:16px;height:16px;border-radius:50%;background:#c4c8cd}
.copy{height:62px;background:var(--darker);color:#8c9197;font-size:12px;text-align:center;line-height:62px}
</style>
</head>
<body>

<div class="topbar">
  <div class="social"><span class="dot"></span><span class="dot"></span><span class="dot"></span><span class="dot"></span></div>
  <div class="contact"><span>&#9742; 1-800-555-0142</span><span>&#9993; hello@marrowind.au</span></div>
</div>
<header class="header">
  <div class="logo"><span class="name">MARROWIND IT</span><span class="sub">CONSULTANCY</span></div>
  <nav class="nav"><span class="active">HOME</span><span>WHO WE ARE</span><span>WHAT WE DO</span><span>BLOG</span><span>CLIENTS</span><span>CAREERS</span><span>GET IN TOUCH</span></nav>
</header>

<section class="hero" role="img" aria-label="Aerial photo of a harbour city skyline with the waterfront">
  <h1>We are a IT consultancy<br>based on Australia</h1>
  <p>We help companies sustainably embrace and reap the benefits of cloud platforms, through transforming practices, skills and technology using DevOps and Security practices.</p>
  <a class="btn">Learn More</a>
  <div class="dots"><span></span><span></span><span></span><span></span></div>
</section>

<section class="split">
  <div class="wrap">
    <div class="text" style="left:0">
      <h2>Welcome to<b>Marrowind IT Consultancy</b></h2>
      <p>Aliquam molestie, mi et imperdiet euismod, dui purus auctor tellus, et interdum lacus lectus et ante. Sed accumsan sollicitudin sapien, sit amet adipiscing turpis gravida ac. In congue, neque ac lobortis volutpat, libero mauris varius mi, vitae suscipit ipsum ligula vitae risus. Duis aliquam nibh a dui iaculis viverra id a velit. Vivamus egestas risus in magna varius commodo.</p>
      <a class="btn">Learn More</a>
    </div>
    <div class="photo" style="right:0" role="img" aria-label="Photo of a business team working together on laptops"></div>
  </div>
</section>

<section class="services">
  <div class="wrap">
    <h2 class="section-title">What we do</h2>
    <p class="section-lead" style="color:#d8e2ec">Aliquam molestie, mi et imperdiet euismod, dui purus auctor tellus, et interdum lacus lectus et ante. Sed accumsan sollicitudin sapien, sit amet adipiscing turpis gravida ac.</p>
    <div class="trio">
      <div class="card">
        <div class="icon"><svg width="44" height="30" viewBox="0 0 44 30"><path d="M11 29a10 10 0 0 1 0-20 13 13 0 0 1 24 3 8.5 8.5 0 0 1-1 17z" fill="#fff"/></svg></div>
        <h3>Cloud Platforms</h3>
        <p>Aenean a nibh eget turpis vehicula tempus ac sed massa. Vestibulum dolor nulla, ultrices ac tincidunt sed..</p>
        <a class="btn-ghost">Learn More</a>
      </div>
      <div class="card">
        <div class="icon"><svg width="40" height="40" viewBox="0 0 40 40" fill="none" stroke="#fff" stroke-width="3"><rect x="3" y="3" width="34" height="34" rx="5"/><path d="M15 14l-6 6 6 6M25 14l6 6-6 6M22 12l-4 16"/></svg></div>
        <h3>Using DevOps</h3>
        <p>Aenean a nibh eget turpis vehicula tempus ac sed massa. Vestibulum dolor nulla, ultrices ac tincidunt sed..</p>
        <a class="btn-ghost">Learn More</a>
      </div>
      <div class="card">
        <div class="icon"><svg width="34" height="40" viewBox="0 0 34 40"><path d="M17 2 32 7v12c0 10-7 16-15 19C9 35 2 29 2 19V7z" fill="#fff"/><path d="M17 6v29c-6-3-11-8-11-16V10z" fill="#22b8eb"/></svg></div>
        <h3>Security Practices</h3>
        <p>Aenean a nibh eget turpis vehicula tempus ac sed massa. Vestibulum dolor nulla, ultrices ac tincidunt sed..</p>
        <a class="btn-ghost">Learn More</a>
      </div>
    </div>
  </div>
</section>

<section class="split who">
  <div class="wrap">
    <div class="photo" style="left:0" role="img" aria-label="Photo of colleagues gathered around a laptop in an office"></div>
    <div class="text" style="right:0;width:500px">
      <h2>Who we are</h2>
      <p>Aliquam molestie, mi et imperdiet euismod, dui purus auctor tellus, et interdum lacus lectus et ante. Sed accumsan sollicitudin sapien, sit amet adipiscing turpis gravida ac. In congue, neque ac lobortis volutpat, libero mauris varius mi, vitae suscipit ipsum ligula vitae risus. Duis aliquam nibh a dui iaculis viverra id a velit. Vivamus egestas risus in magna varius commodo.</p>
      <a class="btn">Learn More</a>
    </div>
  </div>
</section>

<section class="why">
  <div class="wrap">
    <h2 class="section-title">Why choose us</h2>
    <p class="section-lead">Aliquam molestie, mi et imperdiet euismod, dui purus auctor tellus, et interdum lacus lectus et ante. Sed accumsan sollicitudin sapien, sit amet adipiscing turpis gravida ac.</p>
    <div class="trio">
      <div class="card">
        <div class="mark"><i></i>QNT</div>
        <h3>QNT Web Services (QNT)</h3>
        <p>Aenean a nibh eget turpis vehicula tempus ac sed massa. Vestibulum dolor nulla, ultrices ac tincidunt sed..</p>
        <a class="btn-ghost">Learn More</a>
      </div>
      <div class="card">
        <div class="mark"><i></i>Vantrel Skyline</div>
        <h3>Vantrel Skyline</h3>
        <p>Aenean a nibh eget turpis vehicula tempus ac sed massa. Vestibulum dolor nulla, ultrices ac tincidunt sed..</p>
        <a class="btn-ghost">Learn More</a>
      </div>
      <div class="card">
        <div class="mark"><i></i>Horvik Vapor</div>
        <h3>Horvik Vapor</h3>
        <p>Aenean a nibh eget turpis vehicula tempus ac sed massa. Vestibulum dolor nulla, ultrices ac tincidunt sed..</p>
        <a class="btn-ghost">Learn More</a>
      </div>
    </div>
  </div>
</section>

<section class="quote" role="img" aria-label="Dark photo of hands typing on a laptop beside a coffee cup">
  <div class="avatar" role="img" aria-label="Portrait photo of the client"></div>
  <blockquote><b>&ldquo;</b> Aliquam molestie, mi et imperdiet euismod, dui purus auctor tellus, et interdum lacus lectus et ante. Sed accumsan sollicitudin sapien, sit amet adipiscing turpis gravida ac. <b>&rdquo;</b></blockquote>
  <div class="who-name">Name Heading</div>
  <div class="role">Company Name</div>
</section>

<section class="blog">
  <div class="wrap">
    <h2 class="section-title">Blog posts</h2>
    <p class="section-lead" style="margin-top:12px">Aliquam molestie, mi et imperdiet euismod, dui purus auctor tellus, et interdum lacus lectus et ante.</p>
    <div class="posts">
      <article class="post">
        <div class="thumb" role="img" aria-label="Photo of a hand touching a cloud network interface"></div>
        <h3>Sed accumsan sollicitudinad piscing turpis gravida ac.</h3>
        <p>Sed accumsan sollicitudin sapien, sit amet adipiscing turpis gravida ac. Vivamus egestas risus in magna varius commodo. Sed semper viverra egestas.</p>
        <a class="btn">Learn More</a>
      </article>
      <article class="post">
        <div class="thumb" role="img" aria-label="Photo of a team meeting around a wooden table"></div>
        <h3>Sed accumsan sollicitudinad piscing turpis gravida ac.</h3>
        <p>Sed accumsan sollicitudin sapien, sit amet adipiscing turpis gravida ac. Vivamus egestas risus in magna varius commodo. Sed semper viverra egestas.</p>
        <a class="btn">Learn More</a>
      </article>
      <article class="post">
        <div class="thumb" role="img" aria-label="Photo of a phone showing an encrypted security screen"></div>
        <h3>Sed accumsan sollicitudinad piscing turpis gravida ac.</h3>
        <p>Sed accumsan sollicitudin sapien, sit amet adipiscing turpis gravida ac. Vivamus egestas risus in magna varius commodo. Sed semper viverra egestas.</p>
        <a class="btn">Learn More</a>
      </article>
    </div>
  </div>
</section>

<section class="clients">
  <div class="wrap">
    <h2 class="section-title">Our clients</h2>
    <p class="section-lead">Aliquam molestie, mi et imperdiet euismod, dui purus auctor tellus, et interdum lacus lectus et ante.</p>
    <div class="client-row"><span>Greenvale</span><span>Lumora</span><span>Netlink</span><span>Corvo</span><span>Tessaro</span><span>Quill</span><span>Brightforge</span><span>Petrix</span><span>Arvan</span></div>
  </div>
</section>

<footer class="footer">
  <div class="wrap cols">
    <div class="col">
      <h4>Company</h4>
      <ul><li>HOME</li><li>WHO WE ARE</li><li>WHAT WE DO</li><li>BLOG</li><li>CLIENTS</li><li>CAREERS</li><li>GET IN TOUCH</li></ul>
    </div>
    <div class="col">
      <h4>Recent Tweets</h4>
      <div class="tweet"><div class="date">&#9679; AUG 03, 2016</div>Vestibulum ante ipsum primis in faucibus orci luctus et ultrices <a>https://mw.to/R8Dw4YD9</a><br>3hrs ago | Retweets</div>
      <div class="tweet"><div class="date">&#9679; AUG 03, 2016</div>Vestibulum ante ipsum primis in faucibus orci luctus et ultrices <a>https://mw.to/R8Dw4YD9</a><br>3hrs ago | Retweets</div>
    </div>
    <div class="col">
      <h4>Contact Us</h4>
      <ul><li><b>COMPANY NAME</b></li></ul>
      <div style="line-height:1.6;margin-bottom:6px">412 Harbour Lane, Sydney,<br>NSW 2000</div>
      <ul><li>&#9742; 1-800-555-0142</li><li>&#9993; hello@marrowind.au</li></ul>
    </div>
    <div class="col newsletter" style="width:245px">
      <h4>Newsletter Sign Up</h4>
      <div class="input">Enter Email Address</div>
      <div style="overflow:hidden;margin-top:12px"><a class="btn">SIGN UP</a></div>
      <h4 style="margin-top:18px">Connect Us</h4>
      <div class="socials"><span></span><span></span><span></span><span></span><span></span></div>
    </div>
  </div>
</footer>
<div class="copy">Copyright &copy; 2016. Company Name. All Right Reserved</div>

</body>
</html>
```